Business Card for Coastal Tundrabridge Advisory

We need a business card for Coastal Tundrabridge Advisory. The company website address is provided below. The company logo is attached. We provide specialized permafrost services to the mining, transportation, and oil & gas industries. The card should be prepared for:
Matthias Korhonen, PhD.
Coastal Tundrabridge Advisory
PO Box 418259
Quillwater, Alaska 99642
Direct: +1-907-555-0143
Email: mkorhonen@tundrabridgeadvisory.example
Website: www.coastaltundrabridgeadvisory.example

```html
<!DOCTYPE html>
<html lang="en">
<head>
<meta charset="utf-8">
<title>Coastal Tundrabridge Advisory – Business Card</title>
<link rel="stylesheet" href="https://fonts.googleapis.com/css2?family=Roboto:wght@300;400;500;700&display=swap">
<style>
  :root {
    --backdrop: #232323;
    --card: #0f1520;
    --ink: #ffffff;
    --ink-soft: #dfe3ea;
    --emboss: #1b2433;
  }
  * { box-sizing: border-box; margin: 0; padding: 0; }
  html, body {
    width: 1200px; height: 780px; overflow: hidden;
    background: var(--backdrop);
    font-family: "Roboto", Arial, sans-serif;
  }
  .stage {
    width: 1200px; height: 780px;
    display: flex; align-items: center; justify-content: center; gap: 40px;
  }
  .card {
    position: relative;
    width: 520px; height: 297px;
    background: var(--card);
    overflow: hidden;
  }

  /* Front side */
  .corner-bar {
    position: absolute; top: 0; right: 26px;
    width: 12px; height: 46px; background: var(--ink);
  }
  .brand-name {
    position: absolute; left: 30px; top: 40px;
    width: 230px;
    color: var(--ink); font-weight: 500; font-size: 19px;
    line-height: 1.15; letter-spacing: 0.5px; text-transform: uppercase;
  }
  .person {
    position: absolute; right: 50px; top: 24px; text-align: right;
    color: var(--ink);
  }
  .person-name { font-size: 24px; line-height: 1.1; }
  .person-name .first { font-weight: 700; }
  .person-name .last { font-weight: 300; }
  .person-title { font-size: 12px; font-weight: 700; margin-top: 2px; }
  .address {
    position: absolute; left: 30px; top: 168px;
    color: var(--ink-soft); font-size: 12.5px; line-height: 1.4;
  }
  .contacts {
    position: absolute; left: 30px; top: 214px;
    list-style: none; color: var(--ink-soft); font-size: 12px; line-height: 1.55;
  }
  .contacts li { display: flex; align-items: center; gap: 8px; }
  .contacts svg { width: 12px; height: 12px; flex: none; }
  .brand-faint {
    position: absolute; right: 24px; bottom: 28px;
    width: 170px; text-align: right;
    color: var(--emboss); font-weight: 500; font-size: 15px;
    line-height: 1.15; text-transform: uppercase; letter-spacing: 0.5px;
  }

  /* Back side */
  .brand-large {
    position: absolute; left: 0; right: 0; top: 70px; text-align: center;
    color: var(--emboss); font-weight: 500; font-size: 30px;
    line-height: 1.15; text-transform: uppercase; letter-spacing: 1px;
    padding: 0 40px;
  }
  .services {
    position: absolute; left: 0; right: 0; bottom: 34px; text-align: center;
    color: var(--ink);
  }
  .services-heading { font-size: 12px; font-weight: 700; letter-spacing: 0.3px; }
  .services-text { font-size: 11px; font-weight: 400; margin-top: 3px; padding: 0 20px; }
</style>
</head>
<body>
<main class="stage">
  <section class="card card-front" aria-label="Card front">
    <div class="corner-bar"></div>
    <div class="brand-name">Coastal Tundrabridge Advisory</div>
    <div class="person">
      <p class="person-name"><span class="first">Matthias</span> <span class="last">Korhonen</span></p>
      <p class="person-title">PhD</p>
    </div>
    <address class="address" style="font-style:normal">
      PO Box 418259<br>
      Quillwater, Alaska 99642
    </address>
    <ul class="contacts">
      <li>
        <svg viewBox="0 0 12 12" aria-hidden="true"><path d="M3 1 L5 3.5 L4 4.8 Q5 7 7.2 8 L8.5 7 L11 9 L9.8 10.8 Q4.5 11 1.2 2.2 Z" fill="#fff"/></svg>
        +1-907-555-0143
      </li>
      <li>
        <svg viewBox="0 0 12 12" aria-hidden="true"><rect x="0.8" y="2.5" width="10.4" height="7.5" fill="none" stroke="#fff" stroke-width="1.1"/><path d="M0.8 2.8 L6 6.8 L11.2 2.8" fill="none" stroke="#fff" stroke-width="1.1"/></svg>
        mkorhonen@tundrabridgeadvisory.example
      </li>
      <li>
        <svg viewBox="0 0 12 12" aria-hidden="true"><circle cx="6" cy="6" r="5" fill="none" stroke="#fff" stroke-width="1.1"/><ellipse cx="6" cy="6" rx="2.2" ry="5" fill="none" stroke="#fff" stroke-width="0.9"/><path d="M1 6 H11" stroke="#fff" stroke-width="0.9"/></svg>
        www.coastaltundrabridgeadvisory.example
      </li>
    </ul>
    <div class="brand-faint">Coastal Tundrabridge Advisory</div>
  </section>

  <section class="card card-back" aria-label="Card back">
    <div class="brand-large">Coastal Tundrabridge Advisory</div>
    <div class="services">
      <p class="services-heading">OUR SERVICES</p>
      <p class="services-text">We provide specialized permafrost services to the mining, transportation, and oil &amp; gas industries</p>
    </div>
  </section>
</main>
</body>
</html>
```